QVR business card

Need a business card for a company that provides instructional design and elearning development services. The website is here: http://quorvane.studio/

I'm attaching a current logo, as well as the old business card design. While I like to keep it clean, the old design is too simplistic for my liking. The only idea I want to reuse from the old design is placing industry jargon on the back of the card, just need a better way to present it. But if you have other ideas for the back--feel free to experiment.

Please use the colors complementary to the color we have on the website. Thank you!

```html
<!DOCTYPE html>
<html lang="en">
<head>
<meta charset="utf-8">
<title>QVR business card</title>
<link href="https://fonts.googleapis.com/css2?family=Open+Sans:wght@400;600;700;800&family=PT+Sans+Narrow:wght@400;700&display=swap" rel="stylesheet">
<style>
  :root {
    --teal: #13aeaa;
    --teal-dark: #0e9894;
    --gold: #d9c98e;
    --ink: #3a3a3a;
    --white: #ffffff;
    --backdrop: #e9eaea;
  }
  * { box-sizing: border-box; margin: 0; padding: 0; }
  html, body { width: 1200px; height: 716px; overflow: hidden; }
  body {
    background: var(--backdrop);
    font-family: "Open Sans", Arial, sans-serif;
    position: relative;
  }
  .card {
    position: absolute;
    width: 540px;
    height: 310px;
    top: 203px;
    border-radius: 4px;
    overflow: hidden;
    box-shadow: 0 6px 18px rgba(0,0,0,.18);
  }

  /* Back side */
  .card-back { left: 45px; background: var(--teal); color: var(--white); }
  .back-headline {
    position: absolute; left: 34px; top: 40px;
    font-weight: 800; font-size: 50px; line-height: 0.98;
    letter-spacing: 0.5px; text-transform: uppercase;
  }
  .back-headline .big { font-size: 66px; }
  .back-divider {
    position: absolute; left: 218px; top: 40px; width: 1.5px; height: 230px;
    background: var(--white);
  }
  .jargon-list {
    position: absolute; left: 236px; top: 38px; list-style: none;
    font-family: "PT Sans Narrow", "Arial Narrow", sans-serif;
    font-size: 28px; line-height: 1.3; text-transform: uppercase;
  }

  /* Front side */
  .card-front { left: 615px; background: var(--white); }
  .front-waves { position: absolute; inset: 0; }
  .brand {
    position: absolute; left: 40px; top: 72px;
    display: flex; align-items: center; gap: 10px;
  }
  .brand-dot { width: 22px; height: 22px; border-radius: 50%; background: var(--teal); }
  .brand-name {
    font-weight: 700; font-size: 42px; color: var(--gold); letter-spacing: 1px;
  }
  .contact {
    position: absolute; left: 292px; top: 66px;
    padding-left: 14px; border-left: 1.5px solid var(--teal);
    color: var(--ink); font-size: 13px;
  }
  .contact-name { color: var(--teal); font-weight: 700; font-size: 16px; }
  .contact-role { font-size: 13px; margin-bottom: 10px; }
  .contact-line { display: flex; align-items: center; gap: 7px; line-height: 1.5; }
  .contact-line svg { width: 11px; height: 11px; flex: none; }
</style>
</head>
<body>

<section class="card card-back" aria-label="Card back">
  <h2 class="back-headline">How<br>Can<br><span class="big">We</span><br>Help?</h2>
  <div class="back-divider"></div>
  <ul class="jargon-list">
    <li>Mobile Learning SCORM</li>
    <li>Instructional Design LMS</li>
    <li>MOOCs eLearning HTML5</li>
    <li>Adult Learning Theory</li>
    <li>Gamification Classroom</li>
    <li>xAPI Blended Learning</li>
  </ul>
</section>

<section class="card card-front" aria-label="Card front">
  <svg class="front-waves" viewBox="0 0 540 310" preserveAspectRatio="none" aria-hidden="true">
    <path d="M0 150 C 120 170, 260 230, 540 300 L540 310 L0 310 Z" fill="var(--gold)"/>
    <path d="M0 168 C 110 190, 250 240, 540 303 L540 310 L0 310 Z" fill="var(--white)"/>
    <path d="M0 186 C 120 200, 230 220, 300 240 C 380 262, 460 284, 540 298 L540 310 L0 310 Z" fill="var(--teal)"/>
    <path d="M130 200 C 260 230, 420 290, 540 302 L540 306 C 420 296, 260 240, 130 200 Z" fill="var(--white)" opacity=".9"/>
  </svg>

  <div class="brand">
    <span class="brand-dot"></span>
    <span class="brand-name">QVR</span>
  </div>

  <div class="contact">
    <div class="contact-name">Dorian Maselko</div>
    <div class="contact-role">Managing Director</div>
    <div class="contact-line">
      <svg viewBox="0 0 12 12"><path d="M3 1 L5 3.5 L4 5 Q5 7 7 8 L8.5 7 L11 9 L10 11 Q5 11 1 6 Q1 3 3 1 Z" fill="var(--teal)"/></svg>
      555-013-2847
    </div>
    <div class="contact-line">
      <svg viewBox="0 0 12 12"><rect x="1" y="2.5" width="10" height="7" rx="1" fill="var(--teal)"/><path d="M1.5 3 L6 6.5 L10.5 3" stroke="var(--white)" fill="none"/></svg>
      dmaselko@quorvane.studio
    </div>
    <div class="contact-line">
      <svg viewBox="0 0 12 12"><circle cx="6" cy="6" r="5" fill="var(--teal)"/><path d="M1 6 H11 M6 1 V11 M6 1 Q3 6 6 11 M6 1 Q9 6 6 11" stroke="var(--white)" stroke-width=".7" fill="none"/></svg>
      www.quorvane.studio
    </div>
  </div>
</section>

</body>
</html>
```